Biz Card

MARKETING today is the most rapidly changing business discipline. Media options to reach customers, actual customer preferences and consumer buying decisions change by the minute . . . no, by the second. The behavioral data generated by all aspects of the business and the new technologies that put the data to work together produce the potential to generate business intelligence and guide smart resource allocation to influence purchase and retention. However, to realize this potential, marketing professionals at all levels and in all organizations must continuously improve their skills not just from on-the-job training but by learning from masters in the field. The Bright Horizon Guild is the training center that serves this professional development need.model logos:msi.orgama.orgcontentmarketinginstitute.comBook covers on MarketingMetrics, Marketing Anaytics
Industry/Entity Type
Business
Contact Information for Business Card
Roy A. YoungCEOMarketing Science Academyphone: 310-601-4755email: roy@marketingscience.comAddress:437 South Rexford DriveBeverly Hills, CA 89377
Look and feel
Each slider illustrates characteristics of the customer's brand and the style your logo design should communicate.

```html
<!DOCTYPE html>
<html lang="en">
<head>
<meta charset="utf-8">
<title>Bright Horizon Guild – Business Card</title>
<link rel="stylesheet" href="https://fonts.googleapis.com/css2?family=Roboto:wght@400;500;700&display=swap">
<style>
  :root {
    --backdrop: #a9a7a7;
    --card: #fbfbfa;
    --brand-red: #8c2727;
    --brand-grey: #4b4748;
    --text: #3f3c3c;
    --edge: #e6e4e2;
  }
  * { box-sizing: border-box; margin: 0; padding: 0; }
  html, body { width: 1200px; height: 1200px; overflow: hidden; }
  body {
    background: var(--backdrop);
    font-family: "Roboto", Arial, sans-serif;
    position: relative;
  }
  .card {
    position: absolute;
    width: 712px;
    height: 418px;
    background: var(--card);
  }
  .card-front { left: 238px; top: 119px; }
  .card-back  { left: 230px; top: 644px; }

  .front-band {
    position: absolute; left: 0; right: 0; bottom: 0;
    height: 16px; background: var(--brand-red);
  }

  .wordmark {
    position: absolute;
    display: flex;
    align-items: center;
    gap: 18px;
  }
  .wordmark-dot {
    width: 22px; height: 22px; border-radius: 50%;
    background: var(--brand-red);
    flex: none;
  }
  .wordmark-name {
    font-weight: 700;
    color: var(--brand-grey);
    font-size: 31px;
    line-height: 33px;
    letter-spacing: 0.5px;
    text-transform: uppercase;
  }
  .card-front .wordmark { left: 50%; top: 160px; transform: translateX(-50%); }
  .card-front .wordmark-name { font-size: 34px; line-height: 36px; }
  .card-back .wordmark { right: 40px; top: 42px; }

  .side-band {
    position: absolute; left: 0; top: 0; bottom: 0;
    width: 60px; background: var(--brand-red);
  }
  .side-edge {
    position: absolute; left: 60px; top: 0; bottom: 0;
    width: 8px; background: var(--edge);
  }

  .person { position: absolute; left: 98px; top: 196px; }
  .person-name {
    color: var(--brand-red);
    font-weight: 700;
    font-size: 25px;
    line-height: 30px;
  }
  .person-role {
    color: var(--text);
    font-size: 15px;
    margin-top: 9px;
    letter-spacing: 0.5px;
  }

  .contact-list {
    position: absolute; left: 98px; top: 284px;
    list-style: none;
  }
  .contact-item {
    display: flex; align-items: center;
    height: 23.7px;
    color: var(--text);
    font-size: 17.5px;
    white-space: nowrap;
  }
  .contact-icon {
    width: 18px; height: 16px; margin-right: 17px; flex: none;
    fill: var(--brand-red);
  }
</style>
</head>
<body>

  <section class="card card-front" aria-label="Card front">
    <div class="wordmark">
      <span class="wordmark-dot"></span>
      <span class="wordmark-name">Bright<br>Horizon<br>Guild</span>
    </div>
    <div class="front-band"></div>
  </section>

  <section class="card card-back" aria-label="Card back">
    <div class="side-band"></div>
    <div class="side-edge"></div>

    <div class="wordmark">
      <span class="wordmark-dot"></span>
      <span class="wordmark-name">Bright<br>Horizon<br>Guild</span>
    </div>

    <div class="person">
      <p class="person-name">Neil P. Barton</p>
      <p class="person-role">CEO</p>
    </div>

    <ul class="contact-list">
      <li class="contact-item">
        <svg class="contact-icon" viewBox="0 0 18 16" aria-hidden="true">
          <path d="M1 5 C1 2 17 2 17 5 L17 6.5 L13 6.5 L13 5 L5 5 L5 6.5 L1 6.5 Z"/>
          <path d="M4 8 L14 8 L16 15 L2 15 Z"/>
        </svg>
        555-274-0182
      </li>
      <li class="contact-item">
        <svg class="contact-icon" viewBox="0 0 18 16" aria-hidden="true">
          <path d="M1 3 L17 3 L17 13 L1 13 Z M2.5 4.5 L9 9 L15.5 4.5 Z" fill-rule="evenodd"/>
        </svg>
        neil@brighthorizonguild.com
      </li>
      <li class="contact-item">
        <svg class="contact-icon" viewBox="0 0 18 16" aria-hidden="true">
          <circle cx="9" cy="8" r="6.5" fill="none" stroke="var(--brand-red)" stroke-width="1.4"/>
          <ellipse cx="9" cy="8" rx="2.8" ry="6.5" fill="none" stroke="var(--brand-red)" stroke-width="1.2"/>
          <path d="M2.5 8 H15.5 M3.5 4.8 H14.5 M3.5 11.2 H14.5" stroke="var(--brand-red)" stroke-width="1.1"/>
        </svg>
        www.brighthorizonguild.com
      </li>
      <li class="contact-item">
        <svg class="contact-icon" viewBox="0 0 18 16" aria-hidden="true">
          <path d="M9 0.5 C5.5 0.5 3.5 3 3.5 5.8 C3.5 9.5 9 15.5 9 15.5 C9 15.5 14.5 9.5 14.5 5.8 C14.5 3 12.5 0.5 9 0.5 Z M9 3.6 A2.2 2.2 0 1 0 9 8 A2.2 2.2 0 1 0 9 3.6 Z" fill-rule="evenodd"/>
        </svg>
        912 North Calloway Lane Westbrook Heights, CA 89377
      </li>
    </ul>
  </section>

</body>
</html>
```